Verdant Ledger - Paid Surveys publisher portal

• Homepage
• Blank Sub Page (Where content goes in between the header/footer)
• Publisher Application Page, complete with Form
• Survey Wall page

Sites that are in a similar vertical that have interesting designs:
rovabin.com
quillmarsh.com
dovek.com
tarn.io

This is a business-to-business site, and needs to have this type of feel to it. Focus on generating revenue, offer completion, paid surveys is the market.

Format: HTML/CSS

Link to current version of application, and form:
https://gridwaveform.brokelqest.com
https://gridwaveform.brokelqest.com/apply
https://gridwaveform.brokelqest.com/panel/4/morvath_user

Please note that we are changing the brand of this project, the name will be determined shortly but everything else remains. It will likely be Verdant Ledger instead of GridWaveform. We will confirm.

Industry/Entity Type

Market Research

Coding

Coded - Design and coding required

Number of Pages Required

4 page

Font styles to use
Sans Serif

Colors

Designer to choose colors to be used in the design.

```html
<!DOCTYPE html>
<html lang="en">
<head>
<meta charset="utf-8">
<title>GridWaveform – Paid Surveys Publisher Portal</title>
<link rel="stylesheet" href="https://fonts.googleapis.com/css2?family=Lato:wght@400;700;900&display=swap">
<style>
:root{
  --red:#e8534a;
  --red-dark:#d9443b;
  --green:#3dbb8a;
  --ink:#2b2b2b;
  --body:#666;
  --black:#111;
  --soft:#f3f4f8;
  --white:#fff;
  --pink:#f6d3d1;
}
*{box-sizing:border-box;margin:0;padding:0}
html,body{width:1200px;height:3681px;overflow:hidden}
body{font-family:'Lato',sans-serif;color:var(--ink);background:var(--white);position:relative}
.abs{position:absolute}
.btn{position:absolute;display:flex;align-items:center;justify-content:center;background:var(--red);color:var(--white);border-radius:30px;font-weight:700;font-size:15px;text-decoration:none}

/* header */
.site-header{position:absolute;left:0;top:0;width:1200px;height:91px;background:var(--black)}
.brand{position:absolute;display:flex;align-items:center;gap:12px;color:var(--white);font-weight:700;font-size:24px}
.brand-dot{width:46px;height:46px;border-radius:50%;background:var(--red)}
.main-nav a{position:absolute;top:37px;color:#aaa;font-size:15px;text-decoration:none}
.login{left:989px;top:30px;width:110px;height:36px;background:var(--green);font-size:15px}

/* hero */
.hero{position:absolute;left:0;top:91px;width:1200px;height:591px;background:linear-gradient(135deg,#3a4654 0%,#1f2730 45%,#5b636b 75%,#2c3238 100%)}
.hero h1{position:absolute;left:150px;top:118px;width:900px;text-align:center;color:var(--white);font-size:43px;line-height:49px;font-weight:900}
.hero .btn{left:456px;top:292px;width:285px;height:49px;font-size:19px}
.hero-arrow{position:absolute;top:248px}

/* about */
.about h2{position:absolute;left:98px;top:759px;width:560px;font-size:34px;line-height:40px;font-weight:700;text-transform:uppercase;color:var(--ink)}
.about p{position:absolute;left:98px;width:570px;font-size:14px;line-height:29px;color:var(--body)}
.about .btn{left:98px;top:1075px;width:228px;height:42px}
.portrait{position:absolute;border-radius:50%;border:4px solid var(--pink)}

/* brands */
.brands{position:absolute;left:0;top:1212px;width:1200px;height:351px;background:var(--soft)}
.section-title{position:absolute;left:0;width:1200px;text-align:center;font-size:34px;font-weight:700;text-transform:uppercase;color:var(--ink)}
.brand-card{position:absolute;top:175px;width:226px;height:83px;background:var(--white);border:1px solid #ddd;box-shadow:0 2px 6px rgba(0,0,0,.08);display:flex;align-items:center;justify-content:center;gap:10px;font-size:30px;font-weight:700;color:#555}
.brand-card i{width:20px;height:20px;border-radius:50%;background:#555;display:block}

/* testimonials */
.testimonials{position:absolute;left:0;top:1563px;width:1200px;height:444px;background:var(--red)}
.testimonials h2{position:absolute;left:410px;top:78px;font-size:32px;font-weight:700;color:var(--white);text-transform:uppercase}
.testimonials blockquote{position:absolute;left:410px;top:150px;width:670px;color:var(--white);font-size:14px;line-height:25px}
.testimonials .name{position:absolute;left:414px;top:252px;color:var(--white);font-size:14px;font-weight:700;text-transform:uppercase;letter-spacing:.5px}
.dots{position:absolute;left:567px;top:388px;display:flex;gap:6px}
.dots span{width:10px;height:10px;border-radius:50%;border:1px solid var(--white)}
.dots span.on{background:var(--white)}

/* feature */
.feature h3{position:absolute;left:748px;top:2093px;width:360px;font-size:21px;line-height:27px;font-weight:700;text-transform:uppercase}
.feature p{position:absolute;left:748px;width:360px;font-size:13px;line-height:22px;color:var(--body)}
.feature .btn{left:748px;top:2321px;width:136px;height:35px;font-size:14px}

/* news */
.news{position:absolute;left:0;top:2459px;width:1200px;height:824px;background:#f7f7f7}
.news-card{position:absolute;top:157px;width:309px;height:496px;background:var(--white);border:1px solid #e6e6e6}
.news-card .thumb{height:206px;background:linear-gradient(135deg,#f07a6f,#e8534a)}
.news-card h4{margin:22px 18px 0;color:var(--red);font-size:17px;line-height:23px;font-weight:700}
.news-card time{display:block;margin:20px 18px 0;font-size:12px;color:#999}
.news-card p{margin:18px 18px 0;font-size:13px;line-height:24px;color:var(--body)}
.news .btn{left:535px;top:719px;width:128px;height:32px;font-size:14px}

/* footer */
.site-footer{position:absolute;left:0;top:3283px;width:1200px;height:398px;background:var(--black);color:#bbb}
.site-footer .blurb{position:absolute;left:98px;top:158px;width:370px;font-size:11px;line-height:16px;color:#999}
.foot-col h5{position:absolute;top:87px;font-size:15px;font-weight:700;color:var(--white);text-transform:uppercase}
.foot-col a{position:absolute;font-size:12px;color:#aaa;text-decoration:none}
.social{position:absolute;left:977px;top:212px;display:flex;gap:6px}
.social span{width:16px;height:16px;border-radius:3px;background:#bbb}
.copyright{position:absolute;left:98px;top:354px;font-size:11px;color:#aaa}
</style>
</head>
<body>

<header class="site-header">
  <div class="brand" style="left:98px;top:22px"><span class="brand-dot"></span>GridWaveform</div>
  <nav class="main-nav">
    <a style="left:400px">Data</a>
    <a style="left:466px">Products</a>
    <a style="left:567px">About</a>
    <a style="left:643px">Resources</a>
    <a style="left:748px">Contact</a>
  </nav>
  <a class="btn login">Login</a>
</header>

<section class="hero" role="img" aria-label="Photo of a person typing at a desk with analytics on a monitor">
  <h1>We are a B2B company focussing on generating revenue, offer completion, paid surveys is the market</h1>
  <a class="btn">Start Earning Today!</a>
  <svg class="hero-arrow" style="left:40px" width="16" height="30" viewBox="0 0 16 30"><path d="M14 2 2 15l12 13" fill="none" stroke="#fff" stroke-opacity=".6" stroke-width="2"/></svg>
  <svg class="hero-arrow" style="left:1142px" width="16" height="30" viewBox="0 0 16 30"><path d="M2 2l12 13L2 28" fill="none" stroke="#fff" stroke-opacity=".6" stroke-width="2"/></svg>
</section>

<section class="about">
  <h2>Accusamus et iusto odio dignissimos ducimus</h2>
  <p style="top:862px">There are many variations of passages of Lorem Ipsum available, but the majority have suffered alteration in some form, by injected humour, or randomised words which don't look even slightly believable. If you are going to use a passage of Lorem Ipsum, you need to be sure there isn't anything embarrassing hidden in the middle of text.</p>
  <p style="top:984px">All the Lorem Ipsum generators on the Internet tend to repeat predefined chunks as necessary, making this the first true generator on the Internet.</p>
  <a class="btn">Read More Information</a>
  <div class="portrait" role="img" aria-label="Black and white photo of a businessman in a suit and tie" style="left:719px;top:741px;width:384px;height:384px;background:linear-gradient(160deg,#d8d8d8,#7a7a7a 60%,#3c3c3c)"></div>
</section>

<section class="brands">
  <h2 class="section-title" style="top:76px">Popular brands we're promoting</h2>
  <div class="brand-card" style="left:101px"><i></i>Marlow Bank</div>
  <div class="brand-card" style="left:358px">Parcelio</div>
  <div class="brand-card" style="left:616px">Northsoft</div>
  <div class="brand-card" style="left:871px"><i></i>Veltra</div>
</section>

<section class="testimonials">
  <div class="portrait" role="img" aria-label="Photo of a client reading on a laptop" style="left:120px;top:125px;width:192px;height:192px;border-color:#fff;background:linear-gradient(160deg,#cfcfcf,#5a5a5a)"></div>
  <h2>Client Testimonials</h2>
  <blockquote>
    <svg width="18" height="14" viewBox="0 0 18 14"><path d="M0 14V8C0 3 3 0 7 0v3C5 3 4 5 4 7h3v7zm10 0V8c0-5 3-8 7-8v3c-2 0-3 2-3 4h3v7z" fill="#fff"/></svg>
    Aliquam dictum elit vitae mauris facilisis, at dictum urna dignissim. Donec veci lectus vel felis lacinia luctus vitae tow iaculis arcu. Mauris mattis, massa eu porta ultricies. Aliquam dictum elit vitae metj jokas iji kalsa adda ctum urna dignissim.
    <svg width="18" height="14" viewBox="0 0 18 14"><path d="M18 0v6c0 5-3 8-7 8v-3c2 0 3-2 3-4h-3V0zM8 0v6c0 5-3 8-7 8v-3c2 0 3-2 3-4H1V0z" fill="#fff"/></svg>
  </blockquote>
  <div class="name">Minima Veniam</div>
  <svg class="abs" style="left:414px;top:287px" width="100" height="18" viewBox="0 0 100 18">
    <g fill="#fff">
      <path id="star" d="M9 1l2.4 5.2 5.6.6-4.2 3.8 1.2 5.6L9 13.4 4 16.2l1.2-5.6L1 6.8l5.6-.6z"/>
      <use href="#star" x="20"/><use href="#star" x="40"/><use href="#star" x="60"/>
      <path d="M89 1l2.4 5.2 5.6.6-4.2 3.8 1.2 5.6L89 13.4z" />
      <path d="M89 1 86.6 6.2 81 6.8l4.2 3.8-1.2 5.6L89 13.4z" fill="#fff" fill-opacity=".5"/>
    </g>
  </svg>
  <div class="dots"><span class="on"></span><span></span><span></span><span></span></div>
</section>

<section class="feature">
  <div class="abs" role="img" aria-label="Illustration of a laptop and tablet showing survey report dashboards" style="left:98px;top:2098px;width:545px;height:270px;background:linear-gradient(180deg,#2a2a2a,#4a4a4a 85%,#c9c9c9);border-radius:10px"></div>
  <h3>Temporibus autem quibusdam et aut officiis</h3>
  <p style="top:2158px">At vero eos et accusamus et iusto odio dignissimos ducimus qui blanditiis praesentium voluptatum deleniti atque corrupti quos dolores et quas molestias excepturi sint occaecati cupiditate non provident</p>
  <p style="top:2247px">Similique sunt in culpa qui officia deserunt mollitia animi, id est laborum et dolorum fuga.</p>
  <a class="btn">Learn more</a>
</section>

<section class="news">
  <h2 class="section-title" style="top:62px">Latest GridWaveform News</h2>
  <article class="news-card" style="left:101px">
    <div class="thumb" role="img" aria-label="Red-tinted photo of a team at work"></div>
    <h4>Excepteur sint occaecat cupidatat non proident</h4>
    <time>December 18, 2017</time>
    <p>Lorem ipsum dolor sit amet, consectetur adipiscing elit, sed do eiusmod tempor incididunt ut labore et dolore magna aliqua. Ut enim ad minim veniam, quis nostrud exercitation ullamco..</p>
  </article>
  <article class="news-card" style="left:444px">
    <div class="thumb" role="img" aria-label="Red-tinted photo of a group meeting"></div>
    <h4>Temporibus autem quibusdam et aut officiis debitis aut rerum</h4>
    <time>December 11, 2017</time>
    <p>Lorem ipsum dolor sit amet, consectetur adipiscing elit, sed do eiusmod tempor incididunt ut labore et dolore magna aliqua. Ut enim ad minim veniam, quis nostrud exercitation ullamco..</p>
  </article>
  <article class="news-card" style="left:788px">
    <div class="thumb" role="img" aria-label="Red-tinted photo of charts on a laptop"></div>
    <h4>Itaque earum rerum hic tenetur a sapiente delectus</h4>
    <time>November 21, 2017</time>
    <p>Lorem ipsum dolor sit amet, consectetur adipiscing elit, sed do eiusmod tempor incididunt ut labore et dolore magna aliqua. Ut enim ad minim veniam, quis nostrud exercitation ullamco..</p>
  </article>
  <a class="btn">All News</a>
</section>

<footer class="site-footer">
  <div class="brand" style="left:98px;top:87px"><span class="brand-dot"></span>GridWaveform</div>
  <p class="blurb">Nam libero tempore, cum soluta nobis est eligendi optio cumque nihil impedit quo minus id quod maxime placeat facere possimus, omnis voluptas assumenda est, omnis dolor repellendus.</p>
  <div class="foot-col">
    <h5 style="left:545px">Company</h5>
    <a style="left:545px;top:130px">Data</a>
    <a style="left:545px;top:164px">Products</a>
    <a style="left:545px;top:197px">About</a>
    <a style="left:545px;top:231px">Resources</a>
    <a style="left:545px;top:265px">Contact</a>
  </div>
  <div class="foot-col">
    <h5 style="left:768px">Resources</h5>
    <a style="left:768px;top:130px">Surveys</a>
    <a style="left:768px;top:164px">Careers</a>
    <a style="left:768px;top:197px">Press</a>
    <a style="left:768px;top:231px">Privacy</a>
    <a style="left:768px;top:265px">Terms</a>
  </div>
  <div class="foot-col">
    <h5 style="left:977px">Contact Us</h5>
    <a style="left:977px;top:130px">Contact Us</a>
    <a style="left:977px;top:164px">Support</a>
  </div>
  <div class="social"><span></span><span></span><span></span><span></span><span></span></div>
  <p class="copyright">Copyright © 2018 GridWaveform. All rights reserved.</p>
</footer>

</body>
</html>
```